Verpackungsdesign für Wellness- und Saunaprodukte
Zielgruppe
BaFinn ist ein junges Start-Up, das sich auf Wellness- und Saunaprodukte spezialisiert hat. Unsere Zielgruppe besteht zu beinahe gleichen Teilen aus männlichen und weiblichen Personen zwischen 30 und 60 Jahren. Unsere Produkte befinden sich eher im mittel- bis höherpreisigen Segment, daher streben wir ein hochwertiges Design für unsere Verpackungen an. Unsere Produktpalette reicht von Mentholkristallen, Saunaaufgüssen, bis hin zu Textilien für den Wellnessbereich und soll dementsprechend Menschen ansprechen, die sich einen gewissen Luxus im Alltag auch gönnen.
Aufgabenstellung
Inspiriert von der skandinavischen Sauna Kultur, möchten wir Momente der Erholung und
Entspannung in den Alltag unserer Kunden bringen. Die Geschichte des Saunierens ist eng mit der skandinavischen Kultur verbunden und skandinavische Stilelemente sind zeitgemäß und sprechen ein breites Publikum an. Das Design muss auf Dosen/Tiegel , Karton Verpackungen und Flaschen verschiedener Größen adaptierbar sein (siehe Bild im Anhang).
40g Tiegel(transparent) Höhe 40mm Durchmesser 60mm (ohne Deckel Silber gebürstet)
100g Tiegel(transparent) Höhe 53mm Durchmesser 71mm (ohne Deckel Silber gebürstet)
200g Tiegel(transparent) Höhe 65mm Durchmesser 90mm (ohne Deckel Silber gebürstet)
Karton Verpackung 124,5x49x49mm
Karton Verpackung 100x100x100mm
Flaschenetikett 134x67mm (Braunglas, schwarzer Deckel)
Es soll ein passendes Keyvisual erstellt werden.
Im Anhang sieht man die Verpackungen, Dosen, Flaschen sowie unsere ersten Design Entwürfe (an diese Anordnung der Elemente kann sich der Designer orientieren ). Das Logo bleibt wie gegeben. Das Produkt für die Tiegel soll Mentholkristalle sein.

```html
<!DOCTYPE html>
<html lang="de">
<head>
<meta charset="utf-8">
<title>BaFinn – Verpackungsdesign</title>
<link href="https://fonts.googleapis.com/css2?family=Marcellus&family=Montserrat:wght@300;400&family=Roboto+Condensed:wght@400&family=Libre+Baskerville&display=swap" rel="stylesheet">
<style>
  :root{
    --canvas:#ffffff;
    --paper:#f7f7f7;
    --paper-jar:#f1f1f1;
    --band-grey:#d6d8d6;
    --band-mint:#d6e1de;
    --green:#3f7a69;
    --coral:#c4625b;
    --band-rose:#f1d6d7;
    --ink:#2b2b2b;
    --emblem:#d9dbd9;
    --logo-text:#c9cccc;
    --display:"Marcellus", serif;
    --body:"Roboto Condensed", sans-serif;
    --sans:"Montserrat", sans-serif;
    --tag:"Libre Baskerville", serif;
  }
  *{margin:0;padding:0;box-sizing:border-box}
  html,body{width:944px;height:1200px;overflow:hidden;background:var(--canvas)}
  .canvas{position:relative;width:944px;height:1200px}

  .label{position:absolute;background:var(--paper);color:var(--ink);overflow:hidden;
         --accent:var(--green);--band-top:var(--band-grey);--band-bottom:var(--band-grey)}
  .label--rose{--accent:var(--coral);--band-top:var(--band-rose);--band-bottom:var(--band-rose)}
  .band{position:absolute;left:0;right:0}
  .band--top{top:0;background:var(--band-top)}
  .band--bottom{bottom:0;background:var(--band-bottom)}
  .brand-block{position:absolute;background:var(--accent);display:flex;align-items:flex-end;justify-content:center}
  .brand-name{font-family:var(--sans);font-weight:300;color:var(--logo-text);letter-spacing:.02em}
  .tag{position:absolute;bottom:0;background:var(--accent);color:#fff;font-family:var(--tag);
       text-align:center;display:flex;align-items:center;justify-content:center;letter-spacing:.04em;line-height:1.35}
  .emblem{position:absolute;border-radius:50%;background:var(--emblem)}
  .centered{position:absolute;transform:translateX(-50%);text-align:center;white-space:nowrap}
  .title{font-family:var(--display);letter-spacing:.06em;line-height:1}
  .subtitle{font-family:var(--display);letter-spacing:.2em}
  .divider{position:absolute;transform:translateX(-50%);height:1px;
           background:linear-gradient(90deg,transparent,#9a9a9a 20%,#bdbdbd 50%,#9a9a9a 80%,transparent)}
  .col-head{font-family:var(--display);letter-spacing:.16em}
  .copy{position:absolute;transform:translateX(-50%);font-family:var(--body);text-align:center;line-height:1.35;color:#333}
  .copy p + p{margin-top:var(--gap)}
  .amount{font-family:var(--sans);font-weight:400}

  /* bottle label */
  .label--bottle{left:170px;top:395px;width:379px;height:189px}
  .label--bottle .band--top{height:12px}
  .label--bottle .band--bottom{height:21px;--band-bottom:var(--band-mint);background:var(--band-mint)}
  .label--bottle .brand-block{left:162px;top:0;width:55px;height:44px;padding-bottom:6px}
  .label--bottle .brand-name{font-size:8.5px}
  .label--bottle .tag{left:162px;width:55px;height:21px;font-size:5px}
  .label--bottle .copy{width:90px;font-size:4.3px;--gap:10px;text-align:justify;text-align-last:center}

  /* box front */
  .label--box{left:676px;top:123px;width:119px;height:329px}
  .label--box .band--top{height:20px}
  .label--box .band--bottom{height:32px}
  .label--box .brand-block{left:27px;top:0;width:63px;height:63px;padding-bottom:13px}
  .label--box .brand-name{font-size:9.5px}
  .label--box .tag{left:29px;width:63px;height:32px;font-size:5.6px}

  /* jar labels */
  .label--jar{top:837px;width:320px;height:111px;background:var(--paper-jar)}
  .label--jar .band--top{height:10px}
  .label--jar .band--bottom{height:16px}
  .label--jar .brand-block{left:144px;top:0;width:41px;height:32px;padding-bottom:4px}
  .label--jar .brand-name{font-size:6.5px}
  .label--jar .tag{left:134px;width:61px;height:16px;font-size:5px}
  .label--jar .copy{width:72px;font-size:4.1px;--gap:9px;text-align:justify;text-align-last:center}
  .label--menthol{left:92px}
  .label--pomegranate{left:466px}
</style>
</head>
<body>
<main class="canvas">

  <!-- Flaschenetikett -->
  <section class="label label--bottle">
    <div class="band band--top"></div>
    <div class="band band--bottom"></div>
    <div class="brand-block"><span class="brand-name">BaFinn</span></div>

    <div class="centered col-head" style="left:64px;top:32px;font-size:7px">INHALTSSTOFFE</div>
    <div class="copy" style="left:64px;top:54px">
      <p>Lorem ipsum dolor sit amet, consectetuer adipiscing elit, sed diam nonummy nibh euismod tincidunt ut laoreet dolore magna aliquam erat volutpat. Ut wisi enim ad</p>
      <p>Lorem ipsum dolor sit amet, consectetuer adipiscing elit, sed diam nonummy nibh euismod</p>
      <p>Lorem ipsum dolor sit amet, consectetuer adipiscing elit, sed diam nonummy nibh euismod tincidunt ut laoreet dolore magna aliquam erat volutpat. Ut wisi enim ad</p>
    </div>
    <div class="centered amount" style="left:64px;top:143px;font-size:10px">250 ml</div>

    <div class="emblem" role="img" aria-label="Ornament: stilisierte nordische Blüte" style="left:172px;top:60px;width:36px;height:36px"></div>
    <div class="centered title" style="left:190px;top:108px;font-size:17px">NORDISCHE<br>FICHTE</div>
    <div class="divider" style="left:190px;top:148px;width:66px"></div>
    <div class="centered subtitle" style="left:190px;top:154px;font-size:6.5px">AUFGUSS</div>

    <div class="centered col-head" style="left:316px;top:32px;font-size:7px">ANWENDUNG</div>
    <div class="copy" style="left:316px;top:54px">
      <p>Lorem ipsum dolor sit amet, consectetuer adipiscing elit, sed diam nonummy nibh euismod tincidunt ut laoreet dolore magna aliquam erat volutpat. Ut wisi enim ad</p>
      <p>Lorem ipsum dolor sit amet, consectetuer adipiscing elit, sed diam nonummy nibh euismod</p>
      <p>Lorem ipsum dolor sit amet, consectetuer adipiscing elit, sed diam nonummy nibh euismod tincidunt ut laoreet dolore magna aliquam erat volutpat. Ut wisi enim ad</p>
      <p>Lorem ipsum dolor sit amet, consectetuer adipiscing elit, sed diam nonummy nibh euismod tincidunt ut laoreet dolore magna aliquam erat volutpat. Ut wisi enim ad</p>
    </div>

    <div class="tag">FÜR DIE SAUNA</div>
  </section>

  <!-- Kartonverpackung, Vorderseite -->
  <section class="label label--box">
    <div class="band band--top"></div>
    <div class="band band--bottom"></div>
    <div class="brand-block"><span class="brand-name">BaFinn</span></div>
    <div class="emblem" role="img" aria-label="Ornament: stilisierte nordische Blüte" style="left:35px;top:96px;width:49px;height:49px"></div>
    <div class="centered title" style="left:60px;top:176px;font-size:14px">NORDISCHE<br>FICHTE</div>
    <div class="divider" style="left:60px;top:213px;width:64px"></div>
    <div class="centered subtitle" style="left:60px;top:227px;font-size:6.5px">AUFGUSS</div>
    <div class="tag">FÜR<br>DIE SAUNA</div>
  </section>

  <!-- Tiegeletikett Mentholkristalle -->
  <section class="label label--jar label--menthol">
    <div class="band band--top"></div>
    <div class="band band--bottom"></div>
    <div class="brand-block"><span class="brand-name">BaFinn</span></div>
    <div class="centered col-head" style="left:55px;top:23px;font-size:5.6px">INHALTSSTOFFE</div>
    <div class="copy" style="left:55px;top:37px">
      <p>Lorem ipsum dolor sit amet, consectetuer adipiscing elit, sed diam nonummy nibh euismod tincidunt ut laoreet dolore magna aliquam erat volutpat. Ut wisi enim ad</p>
    </div>
    <div class="centered amount" style="left:55px;top:74px;font-size:8px">40 g</div>
    <div class="emblem" role="img" aria-label="Ornament: stilisierte nordische Blüte" style="left:154px;top:40px;width:21px;height:21px"></div>
    <div class="centered title" style="left:165px;top:67px;font-size:8.6px">MENTHOL<br>KRISTALLE</div>
    <div class="divider" style="left:165px;top:88px;width:32px"></div>
    <div class="centered col-head" style="left:266px;top:23px;font-size:5.6px">ANWENDUNG</div>
    <div class="copy" style="left:266px;top:37px">
      <p>Lorem ipsum dolor sit amet, consectetuer adipiscing elit, sed diam nonummy nibh euismod tincidunt ut laoreet dolore magna aliquam erat volutpat. Ut wisi enim ad</p>
      <p>Lorem ipsum dolor sit amet, consectetuer adipiscing elit, sed diam nonummy nibh</p>
    </div>
    <div class="tag">FÜR DIE SAUNA</div>
  </section>

  <!-- Tiegeletikett Granatapfel -->
  <section class="label label--jar label--rose label--pomegranate">
    <div class="band band--top"></div>
    <div class="band band--bottom"></div>
    <div class="brand-block"><span class="brand-name">BaFinn</span></div>
    <div class="centered col-head" style="left:55px;top:23px;font-size:5.6px">INHALTSSTOFFE</div>
    <div class="copy" style="left:55px;top:37px">
      <p>Lorem ipsum dolor sit amet, consectetuer adipiscing elit, sed diam nonummy nibh euismod tincidunt ut laoreet dolore magna aliquam erat volutpat. Ut wisi enim ad</p>
    </div>
    <div class="centered amount" style="left:55px;top:74px;font-size:8px">40 g</div>
    <div class="emblem" role="img" aria-label="Ornament: stilisierte nordische Blüte" style="left:154px;top:40px;width:21px;height:21px"></div>
    <div class="centered title" style="left:165px;top:68px;font-size:8.6px">GRANATAPFEL</div>
    <div class="centered" style="left:165px;top:79px;font-family:var(--body);font-size:5.6px">Meersalzpeeling</div>
    <div class="centered col-head" style="left:266px;top:23px;font-size:5.6px">ANWENDUNG</div>
    <div class="copy" style="left:266px;top:37px">
      <p>Lorem ipsum dolor sit amet, consectetuer adipiscing elit, sed diam nonummy nibh euismod tincidunt ut laoreet dolore magna aliquam erat volutpat. Ut wisi enim ad</p>
      <p>Lorem ipsum dolor sit amet, consectetuer adipiscing elit, sed diam nonummy nibh</p>
    </div>
    <div class="tag">FÜR DEN KÖRPER</div>
  </section>

</main>
</body>
</html>
```